redesign of my existing custom website into Wordpress based website

I need someone to redesign my current website into something more classy, simplistic, modern and on trend. I would like it set up on Wordpress in a way thats easy for me to make my own additions to blogs/price changes and promotion banners. I will also need a page that is password protected so members can login and have access to all my training videos and resources.
website is www.tidewellmamas.com.au

Target Market(s)

new mums

Industry/Entity Type

Fitness

Coding

Coded - Design and coding required

Number of Pages Required

5+ page

Colors
33a6d7

Requirements
Must have
• chic, modern, stylish and simplistic.
• a call to action above the page fold
• mobile friendly conversion
• a pop up message as soon as someone enters my sight offering my free report
• a members page that is password protected containing 3 youtube videos and 6 pdf attachments as resources
• a home page
• a contact us page
• an about us page
• a blog page
• a store page
Nice to have
• some examples of my peers websites that I like:
• www.norapellwick.com
• https://www.9qlr.com
• https://41bytedgarth.com
Should not have
• anything gimmicky

```html
<!DOCTYPE html>
<html lang="en">
<head>
<meta charset="utf-8">
<title>Program – Tidewell Mamas</title>
<link href="https://fonts.googleapis.com/css2?family=Lato:wght@400;700;900&display=swap" rel="stylesheet">
<style>
:root{
  --brand:#33a6d7;
  --brand-dark:#2b93c1;
  --ink:#1f1f1f;
  --text:#444;
  --muted:#777;
  --line:#dcdcdc;
  --band:#eef6fb;
  --white:#fff;
  --hero-a:#2a2628;
  --hero-b:#5c4a4e;
}
*{box-sizing:border-box;margin:0;padding:0}
html,body{width:1200px;height:4412px;overflow:hidden}
body{font-family:"Lato",Arial,sans-serif;color:var(--text);background:var(--white);font-size:13px;line-height:1.6}
ul{list-style:none}
a{color:inherit;text-decoration:none}
.container{width:1006px;margin:0 auto;position:relative}

/* header */
.site-header{height:94px;border-top:4px solid var(--brand);background:var(--white)}
.site-header .container{display:flex;align-items:center;justify-content:space-between;height:90px}
.brand{display:flex;align-items:center;gap:10px;font-size:20px;font-weight:700;color:var(--ink)}
.brand-dot{width:40px;height:40px;border-radius:50%;border:2px solid var(--ink)}
.main-nav{display:flex;align-items:center;gap:34px;font-size:13px;font-weight:700;color:var(--ink);letter-spacing:.3px}
.main-nav .current{color:var(--brand)}
.cart{width:34px;height:34px;border-radius:50%;border:1.5px solid var(--brand);display:flex;align-items:center;justify-content:center}
.login{display:flex;align-items:center;gap:6px}

/* hero */
.hero{height:312px;background:linear-gradient(100deg,var(--hero-a),var(--hero-b) 45%,#3a3033);position:relative;display:flex;align-items:center;justify-content:center}
.hero h1{color:var(--white);font-size:62px;font-weight:900;letter-spacing:1px}
.hero .arrow{position:absolute;top:50%;transform:translateY(-50%)}
.hero .arrow.prev{left:34px}
.hero .arrow.next{right:34px}

.breadcrumb{padding-top:34px;height:70px;border-bottom:1px solid var(--line);font-size:12px;font-weight:700;color:var(--ink)}
.breadcrumb span{color:var(--brand)}

/* feature rows */
.feature{display:flex;align-items:center;justify-content:space-between}
.media{position:relative;flex:none;width:497px;height:294px;display:flex;align-items:center;justify-content:center}
.media.sofa{background:linear-gradient(135deg,#2e2a2c,#6f5c5a 55%,#3b3435)}
.media.bright{background:linear-gradient(135deg,#d9d6d2,#efeae4 60%,#c9c2ba)}
.media.chart{background:linear-gradient(135deg,#c9c9c9,#e0e0e0);border:12px solid #d4d4d4}
.play{width:66px;height:66px;border-radius:50%;background:rgba(0,0,0,.85);display:flex;align-items:center;justify-content:center;border:2px solid rgba(255,255,255,.6)}
.copy{width:450px}
.copy h2{font-size:29px;font-weight:700;color:var(--ink);line-height:1.22;margin-bottom:18px}
.checks li{position:relative;padding-left:24px;margin-bottom:9px;font-size:12.5px;line-height:1.75}
.checks li::before{content:"";position:absolute;left:0;top:4px;width:13px;height:13px;border-radius:50%;background:var(--brand)}
.checks li::after{content:"";position:absolute;left:4px;top:6px;width:3px;height:6px;border:solid var(--white);border-width:0 2px 2px 0;transform:rotate(45deg)}
.checks.spaced li{margin-bottom:34px}
.checks strong{display:block;color:var(--ink);font-size:13px}
.btn{display:inline-block;background:var(--brand);color:var(--white);font-weight:700;font-size:12px;padding:11px 24px;border-radius:22px;letter-spacing:.3px;margin-top:10px}
.checks.spaced + .btn{margin-top:-14px}
.price{font-size:15px;font-weight:700;color:var(--ink);margin-top:14px}
.price-note{font-size:12px;color:var(--muted)}

.intro{height:480px;padding-top:54px;border-bottom:1px solid var(--line)}
.thumbs{display:flex;justify-content:space-between;padding:50px 0 0;height:304px}
.thumb{width:162px;height:190px}
.thumb.t1{background:linear-gradient(135deg,#e43a8a,#f6c6dc)}
.thumb.t2{background:linear-gradient(135deg,#3a3335,#7a6a66)}
.thumb.t3{background:linear-gradient(135deg,#3a3335,#8ea03a)}
.thumb.t4{background:linear-gradient(135deg,#d8d2cb,#8e7f74)}
.thumb.t5{background:linear-gradient(135deg,#b8452f,#e6c79a)}

.row{display:flex;align-items:center}
.row.band{background:var(--band);box-shadow:0 2px 6px rgba(0,0,0,.12)}
.r2{height:394px;margin-bottom:59px}
.r3{height:382px;margin-bottom:62px}
.r4{height:388px;margin-bottom:59px}
.r5{height:323px;margin-bottom:50px}
.r6{height:397px;margin-bottom:53px}
.r7{height:368px;margin-bottom:58px}

/* call to action */
.cta{height:236px;background:var(--brand);color:var(--white);text-align:center;padding-top:44px}
.cta p{font-size:19px;font-weight:700;line-height:1.55}
.cta .btn{background:var(--white);color:var(--ink);margin-top:22px;padding:12px 28px}

/* footer */
.site-footer{padding-top:40px}
.site-footer .cols{display:flex;height:236px}
.foot-brand{width:283px;display:flex;align-items:flex-start;gap:10px;font-size:20px;font-weight:700;color:var(--ink);padding-top:6px}
.foot-col h3{font-size:15px;font-weight:700;color:var(--ink);margin-bottom:10px}
.foot-col li{font-size:11.5px;line-height:1.95}
.quick{width:173px}
.subscribe{width:340px}
.subscribe p{font-size:11.5px;width:230px;line-height:1.7}
.sub-form{display:flex;margin-top:14px}
.sub-form .field{width:168px;height:32px;border:1px solid var(--line);font-size:11px;color:#aaa;padding:7px 9px}
.sub-form .go{background:var(--brand);color:var(--white);font-size:11px;font-weight:700;padding:8px 10px}
.social li{display:flex;align-items:center;gap:12px;margin-bottom:12px}
.social .ico{width:26px;height:26px;border-radius:4px;background:#8a8a8a}
.copyright{border-top:1px solid var(--line);text-align:center;font-size:11px;color:var(--muted);padding-top:22px;height:80px}
</style>
</head>
<body>

<header class="site-header">
  <div class="container">
    <div class="brand"><span class="brand-dot"></span>Tidewell Mamas</div>
    <nav class="main-nav">
      <a href="#">HOME</a><a href="#">ABOUT US</a><a href="#" class="current">PROGRAM</a><a href="#">BLOG</a><a href="#">SHOP</a><a href="#">CONTACT US</a>
      <span class="cart"><svg width="16" height="14" viewBox="0 0 16 14"><path d="M1 1h2.5l2 8h7.5l1.5-6H4.5" fill="none" stroke="#33a6d7" stroke-width="1.6"/><circle cx="6.5" cy="12" r="1.3" fill="#33a6d7"/><circle cx="12" cy="12" r="1.3" fill="#33a6d7"/></svg></span>
      <span class="login"><svg width="11" height="14" viewBox="0 0 11 14"><rect x="0" y="6" width="11" height="8" rx="1" fill="#33a6d7"/><path d="M2.5 6V4a3 3 0 0 1 6 0v2" fill="none" stroke="#33a6d7" stroke-width="1.6"/></svg>LOGIN</span>
    </nav>
  </div>
</header>

<section class="hero" role="img" aria-label="Mum doing a side plank workout in a living room">
  <svg class="arrow prev" width="18" height="34" viewBox="0 0 18 34"><path d="M16 2L2 17l14 15" fill="none" stroke="#fff" stroke-opacity=".6" stroke-width="3"/></svg>
  <h1>PROGRAM</h1>
  <svg class="arrow next" width="18" height="34" viewBox="0 0 18 34"><path d="M2 2l14 15L2 32" fill="none" stroke="#fff" stroke-opacity=".6" stroke-width="3"/></svg>
</section>

<div class="container breadcrumb">HOME &gt;&gt; <span>PROGRAM</span></div>

<section class="container intro">
  <div class="feature">
    <div class="media sofa" role="img" aria-label="Workout video still of a mum exercising on a mat"><span class="play"><svg width="22" height="24" viewBox="0 0 22 24"><path d="M3 2l17 10L3 22z" fill="#fff"/></svg></span></div>
    <div class="copy">
      <h2>What's included in the program?</h2>
      <ul class="checks">
        <li>Our unique 3 stage; cardio, resistance and core, 12 week training program</li>
        <li>Full instructional online workout videos and program cards for each program</li>
        <li>Weekly accountability charts</li>
        <li>Weekly coaching emails</li>
        <li>Nutritionist approved healthy eating guide</li>
        <li>Healthy Family Favourites recipe ebook</li>
      </ul>
      <p class="price">All for just $89</p>
      <p class="price-note">One time only payment</p>
      <a href="#" class="btn">GET STARTED NOW</a>
    </div>
  </div>
</section>

<div class="container thumbs">
  <div class="thumb t1" role="img" aria-label="Healthy eating guide cover"></div>
  <div class="thumb t2" role="img" aria-label="Mum exercising on the floor"></div>
  <div class="thumb t3" role="img" aria-label="Mum lifting dumbbells"></div>
  <div class="thumb t4" role="img" aria-label="Mum seated after a workout"></div>
  <div class="thumb t5" role="img" aria-label="Plated family dinner"></div>
</div>

<section class="row band r2">
  <div class="container feature">
    <div class="copy">
      <h2>What will you need in order to be able to do the program?</h2>
      <ul class="checks">
        <li>An aerobics step</li>
        <li>At least a 2 and 3kg set of dumbbells (heavier if you are stronger)</li>
        <li>A commitment to sticking with the program and achieving some amazing results!</li>
      </ul>
      <a href="#" class="btn">GET STARTED NOW</a>
    </div>
    <div class="media sofa" role="img" aria-label="Video still of step exercise in a living room"><span class="play"><svg width="22" height="24" viewBox="0 0 22 24"><path d="M3 2l17 10L3 22z" fill="#fff"/></svg></span></div>
  </div>
</section>

<section class="row r3">
  <div class="container feature">
    <div class="media sofa" role="img" aria-label="Video still of a floor exercise"><span class="play"><svg width="22" height="24" viewBox="0 0 22 24"><path d="M3 2l17 10L3 22z" fill="#fff"/></svg></span></div>
    <div class="copy">
      <h2>Full Instructional workout videos and program cards</h2>
      <ul class="checks spaced">
        <li><strong>Workout DVD</strong>You will receive a workout DVD that includes all 3 levels of the circuit workouts, so you can follow along doing the workout with us.</li>
        <li><strong>Program Cards</strong>Once your familiar with all the exercises you can switch to using your program cards, which are simply print outs of each exercise program so you can enjoy time with the family while you do your training.</li>
      </ul>
      <a href="#" class="btn">GET STARTED NOW</a>
    </div>
  </div>
</section>

<section class="row band r4">
  <div class="container feature">
    <div class="copy">
      <h2>Weekly accountability charts</h2>
      <ul class="checks">
        <li>The weekly accountability charts tell you exactly how many times per week you should do your circuits as well as some additional core and cardio work</li>
        <li>Place it up on your fridge and tick off each session you do so you can keep track of where you are up to and ensure you complete all the weekly tasks.</li>
      </ul>
      <a href="#" class="btn">GET STARTED NOW</a>
    </div>
    <div class="media chart" role="img" aria-label="Weekly accountability chart sheets"><span class="play"><svg width="22" height="24" viewBox="0 0 22 24"><path d="M3 2l17 10L3 22z" fill="#fff"/></svg></span></div>
  </div>
</section>

<section class="row r5">
  <div class="container feature">
    <div class="media sofa" role="img" aria-label="Video still of a trainer holding dumbbells"><span class="play"><svg width="22" height="24" viewBox="0 0 22 24"><path d="M3 2l17 10L3 22z" fill="#fff"/></svg></span></div>
    <div class="copy">
      <h2>WEEKLY COACHING emails</h2>
      <ul class="checks spaced">
        <li>Stay motivated and on track with your training through the weekly coaching emails from Tidewell Mamas founder and specialist post pregnancy trainer Celia Dunmore.</li>
        <li>You will get an email each week giving extra instructions on what to do each week, how you should be feeling and also lots of advice on how to ensure you keep up your workouts and healthy eating over the 12 weeks.</li>
      </ul>
      <a href="#" class="btn">GET STARTED NOW</a>
    </div>
  </div>
</section>

<section class="row band r6">
  <div class="container feature">
    <div class="copy">
      <h2>Healthy Eating Guide</h2>
      <ul class="checks spaced">
        <li>Leading nutritionist Maren Lowby, from Fernleaf Nutrition provides her expert advice on how to eat a healthy balanced diet that will complement your training and assist your weight loss goals.</li>
        <li>This guide gives you her top 10 healthy eating tips, an eating plan that outlines what your meal portions should look like, loads of tasty ideas for breakfast, lunch and snacks and also additional information for breastfeeding mums on how to bounce back while breast feeding.</li>
      </ul>
      <a href="#" class="btn">GET STARTED NOW</a>
    </div>
    <div class="media sofa" role="img" aria-label="Video still of a mum exercising beside her baby"><span class="play"><svg width="22" height="24" viewBox="0 0 22 24"><path d="M3 2l17 10L3 22z" fill="#fff"/></svg></span></div>
  </div>
</section>

<section class="row r7">
  <div class="container feature">
    <div class="media bright" role="img" aria-label="Mum and baby playing with dumbbells on a mat"><span class="play"><svg width="22" height="24" viewBox="0 0 22 24"><path d="M3 2l17 10L3 22z" fill="#fff"/></svg></span></div>
    <div class="copy">
      <h2>Healthy Family Favourites<br>recipe ebook</h2>
      <ul class="checks spaced">
        <li>Our healthy family favourites ebook is filled with over 30 delicious dinner recipes that will give you plenty of inspiration for ways you can cook low fat meals that will keep the whole family happy.</li>
        <li>The recipes are perfect for busy mums with a number of different options that leave you with plenty of left overs so you don't need to cook every single night.</li>
      </ul>
      <a href="#" class="btn">GET STARTED NOW</a>
    </div>
  </div>
</section>

<section class="cta">
  <p>Let me help you kick start your bounce back journey and get started with the<br>TIDEWELL MAMAS 12 WEEK CHALLENGE today!</p>
  <a href="#" class="btn">GET STARTED NOW</a>
</section>

<footer class="site-footer">
  <div class="container cols">
    <div class="foot-brand"><span class="brand-dot"></span>Tidewell Mamas</div>
    <div class="foot-col quick">
      <h3>Quick Links</h3>
      <ul><li>Home</li><li>About Us</li><li>Program</li><li>Blog</li><li>Shop</li><li>Contact Us</li></ul>
    </div>
    <div class="foot-col subscribe">
      <h3>Subscribe</h3>
      <p>Register your details below and receive tones of free information on fitness and living a healthy lifestyle</p>
      <div class="sub-form"><span class="field">Email Address</span><span class="go">SUBSCRIBE</span></div>
    </div>
    <div class="foot-col">
      <h3>Stay Connected</h3>
      <ul class="social">
        <li><span class="ico"></span>Kinnet</li>
        <li><span class="ico"></span>Snapgrove</li>
        <li><span class="ico"></span>Workloop</li>
      </ul>
    </div>
  </div>
  <div class="container copyright">Copyrights © 2017, Tidewell Mamas. All rights reserved.</div>
</footer>

</body>
</html>
```